Website Home Page for Women's Health Medical Office

Redesign existing homepage for website using existing logo. Current website location is www.meadowcrestwomens.com. Please give it a modern, streamlined, playful feel.

Please give it a feminine feel and make it bright and cheerful using logo colors.

Target Market(s)

Women between the ages of 25-45

Industry/Entity Type

Medical Office

Coding

Coded - Design and coding required

Number of Pages Required

1 page

Font styles to use
Sans Serif
Other font styles liked:
• SEGOI UI script for text and GIL SANS for bold (or their equivilent)

Colors
E54698
E96AAD
F1A4CE
F9D9EA
FCEFF6

Requirements
Must have
• Existing logo. Logo Colors. Feminine, cheerful, simple design. all relevant contact information
Nice to have
• clean lines and streamlined look
Should not have
• Cluttered

```html
<!DOCTYPE html>
<html lang="en">
<head>
<meta charset="utf-8">
<title>Meadowcrest OB/GYN – Personalized Medical Care for Women</title>
<link href="https://fonts.googleapis.com/css2?family=Poppins:ital,wght@0,400;0,500;0,600;0,700;1,500;1,600&display=swap" rel="stylesheet">
<style>
:root{
  --pink:#E5368F;
  --pink-2:#E96AAD;
  --pink-3:#F1A4CE;
  --pink-4:#F9D9EA;
  --pink-5:#FCEFF6;
  --ink:#2b2b2b;
  --text:#444;
  --white:#fff;
  --black:#000;
  --footer-bar:#1c1c1c;
}
*{box-sizing:border-box;margin:0;padding:0}
html,body{width:1200px;height:3750px;overflow:hidden;background:var(--white)}
body{font-family:"Poppins",sans-serif;color:var(--text);position:relative}
.abs{position:absolute}
a{color:inherit;text-decoration:none}
.btn{position:absolute;display:flex;align-items:center;justify-content:center;background:var(--pink);color:var(--white);font-weight:600;border-radius:40px;font-size:22px}
.btn-inline{position:relative;display:inline-flex}

/* header */
.site-header{position:absolute;left:0;top:0;width:1200px;height:170px;border-bottom:1px solid #e6e6e6}
.brand{position:absolute;left:75px;top:55px;display:flex;align-items:center;gap:12px;font-weight:700;font-size:22px;color:var(--ink)}
.brand-dot{width:38px;height:38px;border-radius:50%;background:var(--pink)}
.contact-item{position:absolute;top:30px;display:flex;align-items:flex-start;gap:18px;font-size:14px;font-weight:500;color:var(--ink);line-height:20px}
.contact-icon{width:42px;height:42px;border-radius:50%;background:var(--pink);flex:none;display:flex;align-items:center;justify-content:center}
.main-nav{position:absolute;top:122px;right:72px;display:flex;gap:50px;font-weight:600;font-size:17px;color:var(--ink)}
.main-nav .active{color:var(--pink);border-bottom:2px solid var(--pink);padding-bottom:8px}

/* hero */
.hero{position:absolute;left:0;top:170px;width:1200px;height:670px;overflow:hidden}
.hero-photo{position:absolute;inset:0;background:linear-gradient(110deg,#7b7a76 0%,#b7b1a6 35%,#d9cfc0 60%,#9a928a 100%)}
.hero-title{position:absolute;left:73px;top:190px;color:var(--white);font-weight:700;font-size:56px;letter-spacing:1px}
.hero-sub{position:absolute;left:73px;top:262px;color:var(--white);font-weight:600;font-size:34px;line-height:42px}
.hero-dots{position:absolute;left:77px;top:558px;display:flex;gap:12px}
.hero-dots span{width:12px;height:12px;border-radius:50%;background:var(--pink)}
.hero-dots span:first-child{background:var(--white)}
.hero-wave{position:absolute;left:0;bottom:0}

/* welcome */
.frame-bar{position:absolute;background:var(--pink)}
.photo{position:absolute;border-radius:40px}
.h2{font-weight:700;color:var(--ink);font-size:30px;line-height:36px;letter-spacing:.5px}
.kicker{color:var(--pink);font-style:italic;font-weight:600;font-size:22px}
.body-text{font-size:15px;line-height:30px;color:var(--text)}
.welcome-copy{position:absolute;left:616px;top:900px;width:520px}

/* services */
.services{position:absolute;left:0;top:1523px;width:1200px;height:665px;background:var(--pink-4)}
.service-card{position:absolute;top:210px;width:242px;height:310px;background:var(--white);border-radius:14px;text-align:center;box-shadow:0 4px 12px rgba(229,54,143,.08)}
.service-icon{width:88px;height:88px;border-radius:50%;background:#333;margin:18px auto 0}
.service-card h3{color:var(--pink);font-weight:700;font-size:22px;line-height:29px;margin-top:20px}
.service-card p{font-size:15px;line-height:26px;color:var(--text);margin:14px 24px 0}
.service-btn{position:absolute;top:520px;width:166px;height:52px;border-radius:0 0 14px 14px;background:var(--pink);color:var(--white);font-weight:600;font-size:18px;display:flex;align-items:center;justify-content:center}

/* cta */
.cta{position:absolute;left:0;top:2188px;width:1200px;height:410px;background:linear-gradient(100deg,#b8195f 0%,#e5368f 45%,#f25aa4 100%);text-align:center;color:var(--white)}
.cta h2{font-size:48px;font-weight:700;margin-top:70px}
.cta .l1{font-style:italic;font-weight:500;font-size:27px;margin-top:2px}
.cta .l2{font-style:italic;font-weight:500;font-size:27px;margin-top:18px}
.cta .call{position:absolute;left:477px;top:262px;width:248px;height:64px;border-radius:40px;background:var(--black);color:var(--white);font-weight:600;font-size:22px;display:flex;align-items:center;justify-content:center}

/* footer */
.footer{position:absolute;left:0;top:3250px;width:1200px;height:500px}
.footer-body{position:absolute;left:0;top:140px;width:1200px;height:300px;background:var(--black)}
.footer-col{position:absolute;top:28px;color:var(--white)}
.footer-col h4{font-size:21px;font-weight:600;margin-bottom:8px}
.footer-col li{list-style:none;font-size:14px;line-height:30.5px}
.footer-contact li{display:flex;gap:18px;align-items:flex-start}
.fc-icon{width:12px;height:12px;border-radius:2px;background:var(--pink);margin-top:9px;flex:none}
.footer-bar{position:absolute;left:0;top:440px;width:1200px;height:60px;background:var(--footer-bar);color:var(--white);font-size:13px}
.social{position:absolute;right:70px;top:20px;display:flex;gap:22px}
.social span{width:20px;height:20px;border-radius:50%;background:#cfcfcf}
</style>
</head>
<body>

<header class="site-header">
  <div class="brand"><span class="brand-dot"></span>Meadowcrest OB/GYN</div>
  <div class="contact-item" style="left:387px">
    <span class="contact-icon"><svg width="18" height="18" viewBox="0 0 24 24"><path d="M12 2a7 7 0 0 0-7 7c0 5 7 13 7 13s7-8 7-13a7 7 0 0 0-7-7zm0 9.5A2.5 2.5 0 1 1 12 6.5a2.5 2.5 0 0 1 0 5z" fill="#fff"/></svg></span>
    <span>4810 Larkspur Avenue,<br>Suite 210, Fairhaven,<br>CA 90210</span>
  </div>
  <div class="contact-item" style="left:661px;align-items:center">
    <span class="contact-icon"><svg width="18" height="18" viewBox="0 0 24 24"><path d="M6.6 10.8a15 15 0 0 0 6.6 6.6l2.2-2.2a1 1 0 0 1 1-.25 11.4 11.4 0 0 0 3.6.57 1 1 0 0 1 1 1V20a1 1 0 0 1-1 1A17 17 0 0 1 3 4a1 1 0 0 1 1-1h3.5a1 1 0 0 1 1 1c0 1.25.2 2.45.57 3.57a1 1 0 0 1-.25 1z" fill="#fff"/></svg></span>
    <span>(555) 014-7066</span>
  </div>
  <div class="contact-item" style="left:869px;align-items:center">
    <span class="contact-icon"><svg width="18" height="14" viewBox="0 0 24 18"><rect x="1" y="1" width="22" height="16" rx="2" fill="#fff"/><path d="M2 2l10 8 10-8" stroke="#E5368F" stroke-width="2" fill="none"/></svg></span>
    <span>admin@meadowcrestwomens.com</span>
  </div>
  <nav class="main-nav">
    <a class="active">HOME</a><a>SERVICES</a><a>RESOURCES</a><a>ABOUT US</a><a>CONTACT US</a>
  </nav>
</header>

<section class="hero">
  <div class="hero-photo" role="img" aria-label="Photo of a smiling nurse with a stethoscope showing a tablet to a pregnant patient on a sofa"></div>
  <h1 class="hero-title">MEADOWCREST OB/GYN</h1>
  <p class="hero-sub">Personalized Medical Care<br>For Women</p>
  <a class="btn" style="left:77px;top:382px;width:216px;height:64px">Read More</a>
  <div class="hero-dots"><span></span><span></span><span></span><span></span></div>
  <svg class="hero-wave" width="1200" height="170" viewBox="0 0 1200 170" preserveAspectRatio="none">
    <path d="M0 110 C180 200 420 170 640 120 C850 70 1000 40 1200 110 L1200 170 L0 170Z" fill="#F9D9EA"/>
    <path d="M0 118 C200 190 430 160 650 108 C860 58 1020 20 1200 80 L1200 150 C1020 95 880 120 680 150 C470 180 230 190 0 140Z" fill="#E5368F"/>
    <path d="M0 140 C230 190 470 180 680 150 C880 120 1020 95 1200 150 L1200 170 L0 170Z" fill="#fff"/>
  </svg>
</section>

<section class="welcome">
  <div class="frame-bar" style="left:75px;top:912px;width:330px;height:310px;border-radius:46px 0 0 46px"></div>
  <div class="frame-bar" style="left:178px;top:1380px;width:330px;height:48px;border-radius:0 0 40px 40px"></div>
  <div class="photo" role="img" aria-label="Portrait of a smiling female physician in navy scrubs with arms crossed" style="left:91px;top:929px;width:490px;height:463px;background:linear-gradient(135deg,#6f7a8c,#3b4453 60%,#2a3140);border:6px solid #fff;box-sizing:content-box"></div>
  <div class="welcome-copy">
    <h2 class="h2">WELCOME TO<br>MEADOWCREST OB/GYN, FAIRHAVEN, CA</h2>
    <p class="kicker" style="margin-top:8px">Serving Fairhaven Medical Center</p>
    <p class="body-text" style="margin-top:14px">At Meadowcrest OB/GYN in Fairhaven, California, we believe better health starts when the patient is educated. For this reason, we take time to listen to our patients concerns, explain each option available, and to answer any questions our patients may have so that they can make informed decisions. At Meadowcrest OB/GYN, our providers tailor every procedure performed and treatment option recommended to meet the specific needs of our patients.<br>We remain up-to-date on the latest technology and practice guidelines for women's health.</p>
    <a class="btn btn-inline" style="margin-top:22px;width:216px;height:64px">Read More</a>
  </div>
</section>

<section class="services">
  <h2 class="h2" style="position:absolute;top:88px;width:1200px;text-align:center">HOW CAN WE HELP YOU?</h2>
  <p class="kicker" style="position:absolute;top:140px;width:1200px;text-align:center">Health Services Offered</p>
  <div class="service-card" style="left:75px"><div class="service-icon" role="img" aria-label="Icon of a pregnant woman"></div><h3>PREGNANCY<br>CARE</h3><p>Receiving regular care in pregnancy is important for the health of both you and your baby.</p></div>
  <div class="service-card" style="left:345px"><div class="service-icon" role="img" aria-label="Icon of a birth control pill pack"></div><h3>BIRTH<br>CONTROL</h3><p>Our gynecologists are knowledgeable on all forms of birth control including the IUD.</p></div>
  <div class="service-card" style="left:615px"><div class="service-icon" role="img" aria-label="Icon of a woman with a clipboard"></div><h3>WELL WOMAN<br>EXAMS</h3><p>Our providers will help you to stay healthy by performing a physical exam on you annually.</p></div>
  <div class="service-card" style="left:885px"><div class="service-icon" role="img" aria-label="Icon of women's health"></div><h3>WOMEN'S<br>HEALTH</h3><p>Whether you are dealing with painful or irregular periods, fibroids, or other women's health.</p></div>
  <a class="service-btn" style="left:113px">Read More</a>
  <a class="service-btn" style="left:383px">Read More</a>
  <a class="service-btn" style="left:653px">Read More</a>
  <a class="service-btn" style="left:923px">Read More</a>
</section>

<section class="cta" role="img" aria-label="Pink-tinted photo of a doctor holding a stethoscope to a pregnant belly">
  <h2>Better Health Starts Here!</h2>
  <p class="l1">NOW ACCEPTING NEW PATIENTS</p>
  <p class="l2">Click Here for an Appointment or Call Us At (555) 014-7066</p>
  <a class="call">Call Us Today</a>
</section>

<section class="specialists">
  <div class="abs" style="left:75px;top:2730px;width:520px">
    <h2 class="h2">YOUR OB/GYN SPECIALISTS</h2>
    <p class="body-text" style="margin-top:22px">Meadowcrest OB/GYN offers you the best care possible in a personalized setting. We are currently accepting patients.<br>Call our office now to make an appointment.</p>
    <p class="body-text" style="margin-top:6px">Meadowcrest OB/GYN (located near Fairhaven Hospital in Fairhaven, CA) is a medical office that specializes in Christ-centered healthcare for women of all ages. Our team of exclusively female providers have years of experience taking care of women with a variety of pregnancy and gynecology concerns.</p>
  </div>
  <a class="btn" style="left:75px;top:3061px;width:216px;height:64px">Read More</a>
  <div class="frame-bar" style="left:795px;top:2670px;width:332px;height:305px;border-radius:0 46px 46px 0"></div>
  <div class="frame-bar" style="left:695px;top:3135px;width:330px;height:46px;border-radius:0 0 40px 40px"></div>
  <div class="photo" role="img" aria-label="Photo of a smiling female doctor in a white coat examining a pregnant patient" style="left:609px;top:2687px;width:490px;height:463px;background:linear-gradient(135deg,#eef2f7,#c9d8e6 55%,#8ea7c2);border:6px solid #fff;box-sizing:content-box"></div>
</section>

<footer class="footer">
  <svg class="abs" style="left:0;top:0" width="1200" height="150" viewBox="0 0 1200 150" preserveAspectRatio="none">
    <path d="M0 20 C250 110 520 90 760 50 C960 18 1100 15 1200 30 L1200 150 L0 150Z" fill="#F9D9EA"/>
    <path d="M0 40 C260 130 540 100 780 60 C980 30 1110 30 1200 45 L1200 150 L0 150Z" fill="#E5368F"/>
    <path d="M0 110 C280 150 560 110 800 80 C1000 60 1120 70 1200 80 L1200 150 L0 150Z" fill="#000"/>
  </svg>
  <div class="footer-body">
    <div class="brand" style="left:78px;top:110px;color:#fff"><span class="brand-dot"></span>Meadowcrest OB/GYN</div>
    <div class="footer-col" style="left:380px"><h4>Quick Links</h4><ul><li>Home</li><li>About Us</li><li>News</li><li>Patient Resources</li><li>Privacy Policy</li><li>Contact Us</li></ul></div>
    <div class="footer-col" style="left:623px"><h4>Services</h4><ul><li>Pregnancy Care</li><li>Birth Control</li><li>Well Woman Exams</li><li>Women's Health</li></ul></div>
    <div class="footer-col footer-contact" style="left:860px"><h4>Contact Info</h4><ul>
      <li><span class="fc-icon"></span><span>4810 Larkspur Avenue,<br>Suite 210, Fairhaven, CA 90210</span></li>
      <li><span class="fc-icon"></span><span>(555) 014-7066</span></li>
      <li><span class="fc-icon"></span><span>555-014-7783</span></li>
      <li><span class="fc-icon"></span><span>admin@meadowcrestwomens.com</span></li>
    </ul></div>
  </div>
  <div class="footer-bar">
    <p class="abs" style="left:75px;top:20px">Copyright © 2022. Company Name All rights reserved.</p>
    <div class="social" aria-label="Social media links"><span></span><span></span><span></span><span></span><span></span></div>
  </div>
</footer>

</body>
</html>
```